ORLA - Óptica Médica - web design and concept

Website concept - Create and develop our website design and structure. ORLA is an optical store chain, and we are looking to establish our web and digital concept. In attachment there are several pictures about our stores and our logo.

The website structure should be user friendly. Colors should be light and the design as simple and minimalist as possible. There are different variations of the logothat can be used, check the file.

The website will include optical collections and sun collections as an online store. Also, a medical menu should be considered in order for clients to schedule optometry appointments. There should also be a menu for client assistance where the clients can read about glass maintenance in our workshop.
Updates

Low design quality

Number of Pages Required

5+ page

Font styles to use
Serif
Sans Serif

Requirements
Must have
• Must be user-friendly and minimalist.
• Please USE PICTURES FROM THE BRANDS we sell: MERUN, BOSKA, PNW, KOLE, BAMPE
Nice to have
• Nice to inspire: ZEK glasses (see website https://ch.shopzek.com/en/)
• Nice to inspire: https://merun-eyewear.com/
• Nice to ispire: https://www.pnwglobe.com/en/
Should not have
• Hysteric colors and shapes

```html
<!DOCTYPE html>
<html lang="en">
<head>
<meta charset="utf-8">
<title>ORLA Óptica Médica</title>
<link href="https://fonts.googleapis.com/css2?family=Montserrat:wght@400;500;600;700&display=swap" rel="stylesheet">
<style>
:root{
  --gold:#b8935a;
  --gold-dark:#a88349;
  --ink:#222;
  --text:#333;
  --muted:#777;
  --grey-icon:#5f5f5f;
  --band:#efefef;
  --line:#cfcfcf;
  --white:#fff;
}
*{box-sizing:border-box;margin:0;padding:0}
html,body{width:1200px;height:2804px;overflow:hidden;background:var(--white)}
body{font-family:'Montserrat',sans-serif;color:var(--text);position:relative}
.abs{position:absolute}

/* header */
.site-header{left:0;top:0;width:1200px;height:153px;background:var(--white)}
.brand-name{left:99px;top:20px;font-size:40px;font-weight:500;letter-spacing:6px;color:var(--gold);display:flex;align-items:center;gap:12px}
.brand-name .dot{width:14px;height:14px;border:2px solid var(--gold)}
.header-tools{right:99px;top:27px;display:flex;gap:18px;align-items:center;font-size:15px;font-weight:600;color:var(--gold)}
.tool{display:flex;align-items:center;gap:9px}
.tool-ring{width:38px;height:38px;border:2px solid var(--gold);border-radius:50%;display:flex;align-items:center;justify-content:center}
.header-rule{left:99px;top:92px;width:1002px;height:2px;background:#333}
.main-nav{left:99px;top:113px;width:1002px;display:flex;justify-content:space-around;font-size:16px;font-weight:500;color:var(--ink)}

/* hero */
.hero{left:0;top:153px;width:1200px;height:515px;background:linear-gradient(180deg,#3b3b3d 0%,#545049 45%,#6b4a30 100%)}
.hero-title{left:0;top:246px;width:1200px;text-align:center;font-size:58px;font-weight:700;color:var(--white);letter-spacing:1px}
.hero-text{left:230px;top:340px;width:740px;text-align:center;font-size:15px;line-height:25px;color:var(--white)}
.hero-btn{left:557px;top:424px;width:131px;height:49px;border:2px solid var(--white);border-radius:25px;color:var(--white);font-size:15px;font-weight:500;display:flex;align-items:center;justify-content:center}
.hero-arrow{top:380px}

/* intro cards */
.intro{left:99px;top:572px;width:1004px;height:284px;display:flex;box-shadow:0 4px 10px rgba(0,0,0,.2)}
.intro-card{width:50%;height:100%;text-align:center;padding:40px 40px 0}
.intro-card h2{font-size:28px;font-weight:700;margin-bottom:24px}
.intro-card p{font-size:13.5px;line-height:22px}
.intro-about{background:var(--white)}
.intro-about h2{color:var(--gold)}
.intro-about p{color:var(--ink)}
.intro-call{background:var(--gold);color:var(--white)}
.intro-call p{padding:0 10px;margin-top:-2px}
.pill{display:inline-block;height:41px;line-height:41px;padding:0 18px;border-radius:21px;font-size:15px;font-weight:500}
.intro-about .pill{background:var(--gold);color:var(--white);margin-top:20px}
.intro-call .pill{background:var(--white);color:var(--gold);margin-top:38px;padding:0 30px}

/* section titles */
.section-title{left:0;width:1200px;text-align:center;font-size:30px;font-weight:700;color:var(--gold)}
.title-rule{left:558px;width:84px;height:2px;background:var(--gold)}

/* guarantees */
.guarantee{width:250px;text-align:center}
.guarantee svg{display:block;margin:0 auto}
.guarantee h3{font-size:19px;font-weight:600;line-height:24px;margin:26px 0 14px}
.guarantee p{font-size:13.5px;line-height:19px;color:var(--ink);padding:0 16px}
.g-gold h3{color:var(--gold)}
.g-grey h3{color:var(--grey-icon)}

/* products */
.products-band{left:0;top:1458px;width:1200px;height:589px;background:var(--band)}
.product{width:217px;text-align:center}
.product-photo{width:217px;height:214px;background:radial-gradient(circle,#ffffff 40%,#f1f1f1 100%);border:1px solid #e2e2e2;box-shadow:0 1px 4px rgba(0,0,0,.12)}
.product h4{font-size:16px;font-weight:500;color:var(--ink);margin-top:16px}
.product.is-active h4{color:var(--gold)}
.product p{font-size:12px;line-height:18px;color:var(--muted);margin-top:10px;padding:0 18px}
.product-buy{display:flex;justify-content:space-between;align-items:center;margin-top:22px;padding:0 16px}
.price{font-size:21px;color:var(--ink)}
.add-cart{background:#2d2d2d;color:var(--white);font-size:11px;height:28px;line-height:28px;padding:0 16px;border-radius:14px}
.product.is-active .add-cart{background:var(--gold)}
.slider-arrow{top:1770px}

/* brands */
.brand-row{left:99px;top:2232px;width:1002px;display:flex;justify-content:space-between}
.brand-box{width:188px;height:86px;border:1.5px solid #bbb;display:flex;align-items:center;justify-content:center;font-size:19px;font-weight:700;color:#111;letter-spacing:1px}

/* footer */
.footer{left:0;top:2405px;width:1200px;height:337px;background:linear-gradient(180deg,#f7f7f7,#f1f1f1);border-top:3px solid var(--gold)}
.foot-brand{left:114px;top:2512px;font-size:42px;font-weight:500;letter-spacing:6px;color:var(--gold)}
.payments{left:99px;top:2603px;width:228px;height:55px;background:var(--white);border:1.5px solid #bbb;display:flex;align-items:center;justify-content:space-around;font-size:11.5px;font-weight:700;color:#1a2b6d}
.foot-col h5{font-size:16px;font-weight:600;color:var(--gold);margin-bottom:26px}
.quick-links li{list-style:none;font-size:14px;color:var(--ink);height:32px}
.contact-item{display:flex;gap:18px;margin-bottom:20px}
.contact-item .ring{width:38px;height:38px;border:1.5px solid var(--gold);border-radius:50%;display:flex;align-items:center;justify-content:center;flex:none}
.contact-item strong{display:block;font-size:14px;font-weight:600;color:var(--ink);margin-bottom:6px}
.contact-item span{font-size:12.5px;color:var(--ink);line-height:20px}
.field{background:var(--white);border:1.5px solid #999;border-radius:3px;font-size:11px;color:#444;padding:8px 9px}
.send-btn{background:var(--gold);color:var(--white);font-size:11.5px;font-weight:600;display:flex;align-items:center;justify-content:center}

.bottom-bar{left:0;top:2742px;width:1200px;height:62px;background:#e6e6e6}
.copyright{left:99px;top:2763px;font-size:15px;color:var(--ink)}
.socials{right:99px;top:2752px;display:flex;gap:12px}
.social{display:flex;align-items:center;gap:5px;font-size:12px;color:#111}
.social i{width:14px;height:14px;border:1.5px solid #111;border-radius:50%;display:block}
</style>
</head>
<body>

<header class="site-header abs">
  <div class="brand-name abs">ORLA <span class="dot"></span></div>
  <div class="header-tools abs">
    <div class="tool">
      <span class="tool-ring"><svg width="20" height="18" viewBox="0 0 20 18"><path d="M1 2h3l2 10h10l2-7H5" fill="none" stroke="#b8935a" stroke-width="1.8"/><circle cx="8" cy="15.5" r="1.5" fill="#b8935a"/><circle cx="15" cy="15.5" r="1.5" fill="#b8935a"/></svg></span>
      CART: <span style="font-weight:500">0 ITEMS</span>
    </div>
    <div class="tool">
      <span class="tool-ring"><svg width="20" height="18" viewBox="0 0 20 18"><path d="M10 16S2 11 2 6a4 4 0 0 1 8-1 4 4 0 0 1 8 1c0 5-8 10-8 10z" fill="none" stroke="#b8935a" stroke-width="1.8"/></svg></span>
      WISHLIST
    </div>
  </div>
  <div class="header-rule abs"></div>
  <nav class="main-nav abs">
    <span>HOME</span><span>ABOUT US</span><span>PRODUCTS</span><span>CONTACT</span><span>BLOG</span><span>STORE</span>
  </nav>
</header>

<section class="hero abs" role="img" aria-label="Photo of the ORLA store interior with eyewear displays and wooden counter"></section>
<h1 class="hero-title abs">ORLA OPTICA MEDICA</h1>
<p class="hero-text abs">ORLA OPTICA opens its doors with a clear purpose: to take care of you. Our priority is your visual health, and for this reason we have the best professionals</p>
<div class="hero-btn abs">Read More</div>
<svg class="hero-arrow abs" style="left:34px" width="28" height="50" viewBox="0 0 28 50"><path d="M26 2 3 25l23 23" fill="none" stroke="#fff" stroke-width="2.5"/></svg>
<svg class="hero-arrow abs" style="left:1138px" width="28" height="50" viewBox="0 0 28 50"><path d="M2 2l23 23L2 48" fill="none" stroke="#fff" stroke-width="2.5"/></svg>

<section class="intro abs">
  <div class="intro-card intro-about">
    <h2>ORLA OPTICS</h2>
    <p>ORLA OPTICA opens its doors with a clear purpose: to take care of you. Our priority is your visual health, and for this reason we have the best professionals and the most competitive products to serve your needs.</p>
    <span class="pill">Get to know us better!</span>
  </div>
  <div class="intro-card intro-call">
    <h2>CALL US!</h2>
    <p>BOOK YOUR APPOINTMENT WITH US. We will be happy to help you and offer you the best solution for your visual health problems.</p>
    <span class="pill">Contact</span>
  </div>
</section>

<h2 class="section-title abs" style="top:928px">OUR GUARANTEES</h2>
<div class="title-rule abs" style="top:984px"></div>

<div class="guarantee g-gold abs" style="left:81px;top:1047px">
  <svg width="181" height="177" viewBox="0 0 181 177" role="img" aria-label="Childhood guarantee pictogram"><path d="M90 4 172 52 Q180 58 174 72 L148 160 Q144 172 132 172 H49 Q37 172 33 160 L7 72 Q1 58 9 52Z" fill="#b8935a"/></svg>
  <h3>Orla Childhood<br>Guarantee</h3>
  <p>50% discount on new glasses, if your child's gradua tion has changed before six months.</p>
</div>
<div class="guarantee g-grey abs" style="left:342px;top:1047px">
  <svg width="181" height="177" viewBox="0 0 181 177" role="img" aria-label="Accident warranty pictogram"><path d="M90 4 172 52 Q180 58 174 72 L148 160 Q144 172 132 172 H49 Q37 172 33 160 L7 72 Q1 58 9 52Z" fill="#5f5f5f"/></svg>
  <h3>Orla Accident<br>Warranty</h3>
  <p>Did you get off your glasses when you got out of the car? Did your little boy play with his sunglasses?</p>
</div>
<div class="guarantee g-gold abs" style="left:608px;top:1047px">
  <svg width="181" height="177" viewBox="0 0 181 177" role="img" aria-label="Security guarantee pictogram"><path d="M90 4 172 52 Q180 58 174 72 L148 160 Q144 172 132 172 H49 Q37 172 33 160 L7 72 Q1 58 9 52Z" fill="#b8935a"/></svg>
  <h3 style="margin-top:38px;margin-bottom:26px">Orla Security</h3>
  <p>If you have suffered a robbery or robbery in your home, you will opt for the replacement of the same product.</p>
</div>
<div class="guarantee g-grey abs" style="left:875px;top:1047px">
  <svg width="181" height="177" viewBox="0 0 181 177"><path d="M90 4 172 52 Q180 58 174 72 L148 160 Q144 172 132 172 H49 Q37 172 33 160 L7 72 Q1 58 9 52Z" fill="#5f5f5f"/><path d="M48 88Q90 48 132 88 90 128 48 88Z" fill="#fff"/><circle cx="90" cy="88" r="16" fill="#5f5f5f"/><circle cx="90" cy="88" r="8" fill="#fff"/></svg>
  <h3 style="margin-top:38px;margin-bottom:26px">Orla Vision</h3>
  <p>If you suffer from a diag nosed visual pathology and during the first two years your graduation.</p>
</div>

<div class="products-band abs"></div>
<h2 class="section-title abs" style="top:1505px">OUR PRODUCTS</h2>
<div class="title-rule abs" style="top:1562px"></div>

<svg class="slider-arrow abs" style="left:34px" width="28" height="52" viewBox="0 0 28 52"><path d="M26 2 3 26l23 24" fill="none" stroke="#333" stroke-width="2"/></svg>
<svg class="slider-arrow abs" style="left:1138px" width="28" height="52" viewBox="0 0 28 52"><path d="M2 2l23 24L2 50" fill="none" stroke="#333" stroke-width="2"/></svg>

<div class="product is-active abs" style="left:101px;top:1620px">
  <div class="product-photo" role="img" aria-label="Product photo of black rectangular eyeglasses"></div>
  <h4>Neque porro quisquam</h4>
  <p>Nemo enim ipsam voluptatem quia voluptas sit aspernatur aut.</p>
  <div class="product-buy"><span class="price">$35.90</span><span class="add-cart">Add to Cart</span></div>
</div>
<div class="product abs" style="left:363px;top:1620px">
  <div class="product-photo" role="img" aria-label="Product photo of black eyeglasses"></div>
  <h4>Modi tempora incidunt</h4>
  <p>Nemo enim ipsam voluptatem quia voluptas sit aspernatur aut.</p>
  <div class="product-buy"><span class="price">$35.90</span><span class="add-cart">Add to Cart</span></div>
</div>
<div class="product abs" style="left:624px;top:1620px">
  <div class="product-photo" role="img" aria-label="Product photo of dark round eyeglasses"></div>
  <h4>Minima veniam</h4>
  <p>Nemo enim ipsam voluptatem quia voluptas sit aspernatur aut.</p>
  <div class="product-buy"><span class="price">$35.90</span><span class="add-cart">Add to Cart</span></div>
</div>
<div class="product abs" style="left:886px;top:1620px">
  <div class="product-photo" role="img" aria-label="Product photo of dark eyeglasses"></div>
  <h4>Magni dolores</h4>
  <p>Nemo enim ipsam voluptatem quia voluptas sit aspernatur aut.</p>
  <div class="product-buy"><span class="price">$35.90</span><span class="add-cart">Add to Cart</span></div>
</div>

<h2 class="section-title abs" style="top:2118px">OUR BRANDS</h2>
<div class="title-rule abs" style="top:2175px"></div>
<div class="brand-row abs">
  <div class="brand-box">KESTREL</div>
  <div class="brand-box">MARISOL VEGA</div>
  <div class="brand-box">CORVETTO</div>
  <div class="brand-box">TOMAS LUNE</div>
  <div class="brand-box">BELLARI</div>
</div>

<footer class="footer abs" role="img" aria-label="Faint world map background"></footer>
<div class="foot-brand abs">ORLA</div>
<div class="payments abs"><span>VANTIS</span><span>PayNest</span><span>Skora</span><span>Mondcard</span></div>

<div class="foot-col abs" style="left:393px;top:2457px">
  <h5>QUICK LINKS</h5>
  <ul class="quick-links">
    <li>› Home</li><li>› About Us</li><li>› Products</li><li>› Contact</li><li>› Blog</li><li>› Contact Us</li>
  </ul>
</div>

<div class="foot-col abs" style="left:561px;top:2457px">
  <h5>CONTACT US</h5>
  <div class="contact-item">
    <span class="ring"><svg width="14" height="18" viewBox="0 0 14 18"><path d="M7 17S1 10 1 6.5a6 6 0 0 1 12 0C13 10 7 17 7 17z" fill="none" stroke="#b8935a" stroke-width="1.6"/><circle cx="7" cy="6.5" r="2" fill="#b8935a"/></svg></span>
    <div><strong>ADDRESS,</strong><span>Calle Almendro, 22.<br>Valdeluz</span></div>
  </div>
  <div class="contact-item">
    <span class="ring"><svg width="12" height="18" viewBox="0 0 12 18"><rect x="1" y="1" width="10" height="16" rx="2" fill="none" stroke="#b8935a" stroke-width="1.6"/><circle cx="6" cy="14" r="1" fill="#b8935a"/></svg></span>
    <div><strong>PHONE:</strong><span>900 17 28 46</span></div>
  </div>
  <div class="contact-item">
    <span class="ring"><svg width="16" height="12" viewBox="0 0 16 12"><rect x="1" y="1" width="14" height="10" fill="#b8935a"/><path d="M1 1l7 6 7-6" fill="none" stroke="#fff" stroke-width="1.3"/></svg></span>
    <div><strong>MAIL:</strong><span>orlaoptica@mailbay.com</span></div>
  </div>
</div>

<div class="foot-col abs" style="left:813px;top:2457px"><h5>CONTACT FORM</h5></div>
<div class="field abs" style="left:813px;top:2510px;width:137px;height:34px">Name</div>
<div class="field abs" style="left:961px;top:2510px;width:138px;height:34px">Phone</div>
<div class="field abs" style="left:813px;top:2553px;width:286px;height:64px">Message</div>
<div class="send-btn abs" style="left:813px;top:2635px;width:118px;height:36px">SEND MESSAGE</div>

<div class="bottom-bar abs"></div>
<div class="copyright abs">Copyright © 2018 Orla Optica. All Rights Reserved.</div>
<div class="socials abs">
  <span class="social"><i></i>Nookly</span>
  <span class="social"><i></i>Pinlo</span>
  <span class="social"><i></i>Chirpa</span>
  <span class="social"><i></i>Gloop</span>
  <span class="social"><i></i>Linkra</span>
</div>

</body>
</html>
```